RWT Fittings Ltd Business Cards

We need a business card with our business logo. We provide window and door installations on high-rises in west coast British Colombia, Canada.

I would like my business information and details on one side of the card, and the other side the company name with logo

Target Market(s)

General Contractors

Industry/Entity Type

Construction

Contact Information for Business Card

one side i want my company name and logo in the dark theme logo that i provided

Requirements
Must have
• Marco Peltieri, 16045518293, RWTFittings@mailbox-demo.com, 1407-5194 Linden Row Burnaby BC, V5H 2K9, Owner & Manager

```html
<!DOCTYPE html>
<html lang="en">
<head>
<meta charset="utf-8">
<title>RWT Fittings Ltd Business Cards</title>
<link href="https://fonts.googleapis.com/css2?family=Quicksand:wght@500;600;700&display=swap" rel="stylesheet">
<style>
  :root {
    --backdrop-light: #8a8a8a;
    --backdrop-dark: #4a4a4a;
    --card-white: #ffffff;
    --card-dark: #1a1a1a;
    --card-dark-2: #2e2d2c;
    --brand-blue: #2fa8e0;
    --brand-grey: #9a9a9a;
    --text-grey: #5a5a5a;
  }
  * { box-sizing: border-box; margin: 0; padding: 0; }
  html, body { width: 1200px; height: 876px; overflow: hidden; }
  body {
    background: radial-gradient(ellipse at 40% 35%, var(--backdrop-light), var(--backdrop-dark));
    font-family: "Quicksand", sans-serif;
    display: flex;
    align-items: center;
    justify-content: center;
    gap: 50px;
  }
  .card {
    width: 525px;
    height: 300px;
    border-radius: 4px;
    position: relative;
    overflow: hidden;
    box-shadow: 0 18px 40px rgba(0,0,0,0.35);
  }
  /* contact side */
  .card--contact { background: var(--card-white); }
  .contact-info { position: absolute; left: 32px; top: 30px; width: 285px; }
  .wordmark {
    display: flex; align-items: center; gap: 10px;
    color: var(--brand-blue); font-weight: 700; font-size: 22px; letter-spacing: 0.5px;
    white-space: nowrap;
  }
  .wordmark__square { width: 22px; height: 22px; background: var(--brand-blue); flex: none; }
  .person-name {
    margin-top: 26px;
    color: var(--brand-blue); font-weight: 600; font-size: 24px; letter-spacing: 1.5px;
    text-transform: uppercase; white-space: nowrap;
  }
  .person-role { color: var(--text-grey); font-size: 13px; font-weight: 600; margin-top: 2px; }
  .address { color: var(--text-grey); font-size: 13px; font-weight: 500; line-height: 1.45; margin-top: 10px; }
  .contact-list { list-style: none; margin-top: 10px; color: var(--text-grey); font-size: 13px; font-weight: 500; }
  .contact-list li { display: flex; align-items: center; gap: 7px; line-height: 1.55; white-space: nowrap; }
  .contact-list svg { width: 11px; height: 11px; fill: var(--brand-blue); flex: none; }
  .brand-decoration {
    position: absolute; right: 0; top: 0; width: 200px; height: 100%;
    background: linear-gradient(160deg, var(--brand-grey) 0%, var(--brand-grey) 50%, var(--brand-blue) 75%);
  }
  /* logo side */
  .card--logo {
    background: linear-gradient(135deg, var(--card-dark) 0%, var(--card-dark-2) 60%, var(--card-dark) 100%);
    display: flex; align-items: center; justify-content: center;
  }
  .card--logo .wordmark { font-size: 34px; gap: 14px; }
  .card--logo .wordmark__square { width: 32px; height: 32px; }
</style>
</head>
<body>
  <section class="card card--contact">
    <div class="contact-info">
      <div class="wordmark"><span class="wordmark__square"></span>RWT Fittings Ltd</div>
      <p class="person-name">Marco Peltieri</p>
      <p class="person-role">Owner &amp; Manager</p>
      <p class="address">1407-5194 Linden Row, Burnaby<br>British Columbia, V5H 2K9</p>
      <ul class="contact-list">
        <li><svg viewBox="0 0 24 24"><path d="M6.6 10.8a15.1 15.1 0 0 0 6.6 6.6l2.2-2.2a1 1 0 0 1 1-.25 11.4 11.4 0 0 0 3.6.57 1 1 0 0 1 1 1V20a1 1 0 0 1-1 1A17 17 0 0 1 3 4a1 1 0 0 1 1-1h3.5a1 1 0 0 1 1 1c0 1.25.2 2.45.57 3.57a1 1 0 0 1-.25 1z"/></svg>(604) 551-8293</li>
        <li><svg viewBox="0 0 24 24"><path d="M2 5h20v14H2z M2 5l10 8 10-8" fill="none" stroke="#2fa8e0" stroke-width="2.5"/></svg>RWTFittings@mailbox-demo.com</li>
        <li><svg viewBox="0 0 24 24"><circle cx="12" cy="12" r="10"/></svg>RWTfittings-demo.com</li>
      </ul>
    </div>
    <div class="brand-decoration" role="img" aria-label="Large grey and blue brand symbol decoration"></div>
  </section>

  <section class="card card--logo">
    <div class="wordmark"><span class="wordmark__square"></span>RWT Fittings Ltd</div>
  </section>
</body>
</html>
```